AGP letterhead

We need a letterhead design for our new company based in Los Angeles called "Amber Gate Pictures". We develop film and television projects. We work with investors, financiers, film production companies, film distribution and sales companies as well as studios. We would like to incorporate our logo (see attached) but make the letterhead simple and elegant. We need to include: logo, company address, phone number and company website.
Updates

Hello designers, Thanks for your submissions. For our letterhead, we are looking for something more simple and elegant. No heavy bars or lines. Make it feel light and clean. Not a lot of ink on the page. Use the logo and contact info but think "clean", "streamlined" and mostly white paper. Looking forward to seeing more... thanks! Amber Gate Pictures team

Target Market(s)

Studio executives, talent agents and agencies, financiers, investors.

Industry/Entity Type

It Company

Requirements
Must have
• Amber Gate Pictures logo (see attached). Logo may be cropped and altered appropriately for elegant letterhead design.
• Please include:
• COMPANY ADDRESS:
• Tolvane Arts Park
• 2850 Delmore Street
• Crest Hall, 2nd Floor
• Larkmoor Bay, CA 90417
• COMPANY WEBSITE:
• www.ambergatepicturesco.example
• COMPANY PHONE NUMBER:
• 555-604-2187

```html
<!DOCTYPE html>
<html lang="en">
<head>
<meta charset="utf-8">
<title>Amber Gate Pictures – Letterhead</title>
<link rel="stylesheet" href="https://fonts.googleapis.com/css2?family=Source+Sans+3:wght@400;700&display=swap">
<style>
  :root {
    --backdrop: #e4e4e2;
    --paper: #ffffff;
    --brand-dark: #0f1a22;
    --brand-blue: #1f79c4;
    --address-blue: #2c6fd8;
    --ink-grey: #3f4447;
    --icon-grey: #8a8f93;
    --band-top: #f6f7f7;
    --band-bottom: #eceeef;
  }
  * { margin: 0; padding: 0; box-sizing: border-box; }
  html, body {
    width: 950px;
    height: 1200px;
    overflow: hidden;
    background: var(--backdrop);
    font-family: "Source Sans 3", sans-serif;
  }
  .letterhead {
    position: absolute;
    left: 51px;
    top: 50px;
    width: 848px;
    height: 1098px;
    background: var(--paper);
  }
  .brand {
    position: absolute;
    top: 26px;
    left: 0;
    width: 100%;
    display: flex;
    flex-direction: column;
    align-items: center;
  }
  .brand-mark {
    width: 110px;
    height: 110px;
    border-radius: 50%;
    background: var(--brand-dark);
  }
  .brand-name {
    margin-top: 6px;
    font-size: 17px;
    line-height: 20px;
    font-weight: 700;
    letter-spacing: 1px;
    text-transform: uppercase;
    color: var(--brand-blue);
  }
  .contact-band {
    position: absolute;
    left: 0;
    bottom: 0;
    width: 100%;
    height: 63px;
    text-align: center;
  }
  .contact-address {
    height: 31px;
    line-height: 31px;
    background: var(--band-top);
    font-size: 14.5px;
    color: var(--address-blue);
  }
  .contact-lines {
    height: 32px;
    background: var(--band-bottom);
    display: flex;
    justify-content: center;
    align-items: center;
    gap: 6px;
    color: var(--ink-grey);
  }
  .contact-phone { font-size: 14px; }
  .contact-web { font-size: 16px; }
  .contact-icon { width: 10px; height: 10px; flex: none; }
</style>
</head>
<body>
  <main class="letterhead">
    <header class="brand">
      <div class="brand-mark"></div>
      <div class="brand-name">Amber Gate Pictures</div>
    </header>

    <footer class="contact-band">
      <p class="contact-address">Tolvane Arts Park 2850 Delmore Street Crest Hall, 2nd Floor Larkmoor Bay, CA 90417</p>
      <div class="contact-lines">
        <svg class="contact-icon" viewBox="0 0 10 10" aria-hidden="true">
          <path d="M2.3 1 L3.8 2.6 L3 3.6 Q4 5.8 6.3 7 L7.3 6.2 L9 7.7 L8 9 Q3.5 8.6 1 2 Z" fill="none" stroke="var(--icon-grey)" stroke-width="0.9"/>
        </svg>
        <span class="contact-phone">(555)604-2187</span>
        <svg class="contact-icon" viewBox="0 0 10 10" aria-hidden="true" style="margin-left:6px">
          <circle cx="5" cy="5" r="4.2" fill="none" stroke="var(--icon-grey)" stroke-width="0.9"/>
          <ellipse cx="5" cy="5" rx="1.8" ry="4.2" fill="none" stroke="var(--icon-grey)" stroke-width="0.7"/>
          <line x1="0.8" y1="5" x2="9.2" y2="5" stroke="var(--icon-grey)" stroke-width="0.7"/>
        </svg>
        <span class="contact-web">www.ambergatepicturesco.example</span>
      </div>
    </footer>
  </main>
</body>
</html>
```